Web design for new streaming audio service

We need a homepage design for a new streaming audio service. Our company is called Dunmoral, and we’re basically Vexlo for Audiobooks, Stand-Up Comedy, Lectures, Language Learning, etc. Essentially like Plumtrek for everything audio EXCEPT music.
You don’t have to code the homepage (Design Only), but it should include 3 different designs to work with 1) Web; 2) Phones; 3) Tablets.
Below is a link to a mockup of the web version which gives a good idea of what elements we want. This is just a mockup and we want you to improve it.
Once you download the mockup, please refer to the more detailed instructions below:
The following outlines the design project for the Dunmoral homepage. We have provided a rough mockup of the homepage layout that gives you a general idea of what we’re going for. There are a few elements that we are attached to, and many others where you have complete creative freedom to do whatever you think looks good.
The ZIP file includes the following:
* Mockup to see what we have in mind (dunmoral-homepage-mockup.jpg)
* Text used (dunmoral-homepage-text.txt)
* Raw image of actor (dunmoral-actor1.jpg)
* Raw images for samples (dunmoral-sample-[name].jpg)
Although we have only provided a mockup layout for the web version, we also need you to provide a mobile phone and a tablet version of the design also. It’s very possible the tablet version may be substantially similar to the web version, but the mobile phone version will likely be much different.
All of the raw files are included in the attached ZIP file. Please use our photographs and text as provided although cropping, sizing, etc. is flexible per the instructions below.
Display Requirements:
* Web Version - Minimum resolution 1024x768 (72 dpi) but should look good on 1920x1080 (72 dpi) - Page should be designed to scale to look acceptable in all resolutions in between.
* Phone Version - Minimum Zarno 4 - 640x960 (326 dpi) but should look good on Harlow Quasar T5 - 1920x1080 (441 dpi) - Page should be designed to scale to look acceptable in all resolutions and devices in between.
* Tablet Version - Minimum Bristly Ember QX 7” - 1280x800 (216 dpi) but should also look good on a Tavo Breeze - 2048x1536 (264 dpi) - Page should be designed to scale to look acceptable in all resolutions and devices in between.
Above the Fold - We want to make sure the Dunmoral logo, Member Login Link, Large Photo, Headline, Price, Button, and the first row of sample images are all “Above the fold”. As a general guideline, this means 600 pixels high on a 1024x768 72 dpi web screen. This requirement is less important on Phone versions.
Top Logo Bar - We want to retain the blue bar with the Dunmoral logo on the page, although we are open to a different size, shape and positioning if it greatly enhances the design. Please use the standard logo color, although you are welcome to use either the horizontal or vertical orientation of the logo based on your design.
Text color, font and size - Feel free to design the text in anyway you choose as long as the text is readable on the target platforms.
Buttons - Feel free to use any size, shape and colors for the buttons as long as they are obvious and clickable relative to the page. The only exception is the Chatterly button should follow the Chatterly color scheme and logo treatment (the mockup doesn’t seem 100% correct.)
Top Photograph - We want to retain the large photograph across the top of the screen although final shape and dimensions are flexible.
Size and shape of content samples (i.e. Audiobooks, Stand-Up Comedy, etc.) - Feel free to design the content samples in anyway you choose.
Three Sales Points (i.e. Listen on your Zarno…, All you can enjoy…, etc.) - The Three Sales Points are envisioned to each have a corresponding illustration which you should provide and have rights for. The placeholder is represented by a square next to the text. The color size and shape of these elements are flexible and can be designed in any way you choose.
Opt-in form - Feel free to design the opt-in form in anyway you choose as long as the text is readable and the interactivity is obvious on the target platforms.
Text links and copyright notice - Feel free to design the bottom of the page text links and copyright notice in anyway you choose.
Additional colors, graphic design elements, etc. - Feel free to use any additional colors, graphic design elements, etc. to support your design.
people who want to listen to audio through their mobile devices.
Graphic Design

```html
<!DOCTYPE html>
<html lang="en">
<head>
<meta charset="utf-8">
<title>Dunmoral – Unlimited listening</title>
<link rel="stylesheet" href="https://fonts.googleapis.com/css2?family=Signika:wght@300;400;600&family=Open+Sans:wght@400;600;700&display=swap">
<style>
:root{
  --bar:#6fb1d9;
  --band:#5aa3cf;
  --navy:#2b5d80;
  --gold:#a6875a;
  --ink:#333;
  --muted:#8a8a8a;
  --orange:#f2901e;
  --social:#3d5a98;
  --footer:#333436;
  --page:#f7f7f7;
}
*{box-sizing:border-box;margin:0;padding:0}
html,body{width:678px;height:1200px;overflow:hidden;background:var(--page);font-family:"Open Sans",Arial,sans-serif;color:var(--ink)}
.page{position:relative;width:678px;height:1200px}
.hero{position:absolute;left:0;top:0;width:678px;height:448px;background:linear-gradient(100deg,#fbfaf8 0%,#f3efea 38%,#d9c7b4 58%,#b99f88 72%,#7d8cab 100%)}
.hero-photo{position:absolute;right:0;top:0;width:420px;height:448px;background:radial-gradient(ellipse at 60% 40%,rgba(214,170,135,.85),rgba(214,170,135,0) 60%),linear-gradient(180deg,rgba(0,0,0,0) 60%,rgba(70,90,140,.7) 100%)}
.topbar{position:absolute;left:10px;top:10px;width:656px;height:56px;background:var(--bar);border-top:3px solid #2e3236}
.brand{position:absolute;left:14px;top:10px;display:flex;align-items:center;gap:8px;font-family:"Signika",sans-serif;font-weight:600;font-size:28px;color:#fff}
.brand-dot{width:22px;height:22px;border-radius:50%;background:#fff}
.login{position:absolute;right:18px;top:0;width:118px;height:26px;background:#2e3236;border-radius:0 0 12px 12px;color:#fff;font-size:11px;font-weight:600;display:flex;align-items:center;justify-content:center}
.hero-copy{position:absolute;left:24px;top:138px}
.hero-copy h1{font-family:"Signika",sans-serif;font-weight:600;font-size:32px;line-height:36px;color:var(--gold)}
.hero-copy h2{font-family:"Signika",sans-serif;font-weight:300;font-size:32px;line-height:36px;color:var(--gold)}
.price{font-family:"Signika",sans-serif;font-size:16px;margin-top:6px;color:#222}
.btn-trial{display:block;margin-top:14px;width:171px;height:29px;background:linear-gradient(#4a4a4a,#262626);color:#fff;font-family:"Signika",sans-serif;font-size:13.5px;border:1px solid #111;text-align:center;line-height:27px}
.note{margin-top:8px;font-size:8px;color:var(--orange)}
.section-title{position:absolute;left:11px;width:656px;display:flex;align-items:center;gap:10px;font-family:"Signika",sans-serif;font-size:16px;color:#444;white-space:nowrap}
.section-title::before,.section-title::after{content:"";flex:1;height:3px;border-top:1px solid #ddd;border-bottom:1px solid #ddd}
.samples{position:absolute;left:11px;top:501px;width:656px;display:grid;grid-template-columns:repeat(4,152px);column-gap:15.3px;row-gap:17px}
.tile{position:relative;height:99px;box-shadow:0 3px 3px rgba(0,0,0,.12)}
.tile span{position:absolute;left:0;right:0;bottom:0;height:24px;background:rgba(20,30,40,.75);color:#fff;font-size:10.5px;line-height:24px;padding-left:9px}
.t1{background:linear-gradient(135deg,#1c2a30,#4d5c5e)}
.t2{background:linear-gradient(135deg,#6e6a66,#3b3836)}
.t3{background:linear-gradient(135deg,#1e9de0,#1481c4)}
.t4{background:linear-gradient(135deg,#dfe1e3,#9aa6ad)}
.t5{background:linear-gradient(180deg,#6c3a8e,#c45aa8)}
.t6{background:linear-gradient(135deg,#7a3a1e,#2e2a3a)}
.t7{background:linear-gradient(135deg,#b99b70,#5b3a3a)}
.t8{background:linear-gradient(135deg,#6fc3d8,#2c94b4)}
.band{position:absolute;left:0;top:762px;width:678px;height:148px;background:var(--band);border-top:2px solid #4b92bf;border-bottom:2px solid #4b92bf}
.point{position:absolute;top:39px;width:181px;height:85px;background:#fff;text-align:center;padding:10px 12px 0}
.point h3{font-size:8px;font-weight:600;line-height:13px;color:#333}
.point p{font-size:7px;line-height:11.5px;color:#999;margin-top:4px}
.hex{position:absolute;top:19px;width:34px;height:36px}
.trial-copy{position:absolute;left:0;top:973px;width:678px;text-align:center;font-size:12.5px;line-height:17.5px;color:#999}
.trial-note{position:absolute;left:0;top:1016px;width:678px;text-align:center;font-size:10px;font-weight:600;color:#444}
.email{position:absolute;left:142px;top:1044px;width:396px;height:30px;border:1px solid #ddd;background:#fff;font-size:9.5px;font-style:italic;color:#bbb;padding:8px 7px}
.btn-access{position:absolute;left:142px;top:1096px;width:165px;height:31px;background:var(--orange);border:1px solid #e0801a;color:#fff;font-size:11px;font-weight:600;text-align:center;line-height:29px}
.or{position:absolute;left:318px;top:1105px;font-size:9px;color:#999}
.btn-social{position:absolute;left:373px;top:1097px;width:165px;height:29px;background:var(--social);color:#fff;font-size:11px;font-weight:600;display:flex;align-items:center}
.btn-social i{display:block;width:27px;height:29px;background:#2f4a80;margin-right:8px;position:relative}
.btn-social i::after{content:"";position:absolute;left:9px;top:10px;width:9px;height:9px;background:#fff}
.footer{position:absolute;left:0;top:1166px;width:678px;height:34px;background:var(--footer);color:#aaa;font-size:8px;display:flex;justify-content:space-between;align-items:center;padding:0 11px}
.footer nav a{color:#aaa;text-decoration:none}
.footer nav b{font-weight:400;margin:0 4px}
</style>
</head>
<body>
<div class="page">
  <section class="hero">
    <div class="hero-photo" role="img" aria-label="Smiling young man with headphones listening on his phone"></div>
    <header class="topbar">
      <div class="brand"><span class="brand-dot"></span>Dunmoral</div>
      <a class="login">MEMBER LOGIN</a>
    </header>
    <div class="hero-copy">
      <h1>Unlimited listening.</h1>
      <h2>Wherever you are.</h2>
      <p class="price">Only $9.99 per month</p>
      <a class="btn-trial">START YOUR FREE TRAIL</a>
      <p class="note">*Credit Card Not Required</p>
    </div>
  </section>

  <h2 class="section-title" style="top:463px">A Sample of what you can listen to on dunmoral</h2>
  <div class="samples">
    <div class="tile t1" role="img" aria-label="Audio book cover"><span>Audio Books</span></div>
    <div class="tile t2" role="img" aria-label="Comedy album cover"><span>Stand-Up Comedy</span></div>
    <div class="tile t3" role="img" aria-label="Language course cover"><span>Language Learning</span></div>
    <div class="tile t4" role="img" aria-label="Memoir cover"><span>Biographies &amp; Memoris</span></div>
    <div class="tile t5" role="img" aria-label="Relaxation audio cover"><span>Guided Meditations</span></div>
    <div class="tile t6" role="img" aria-label="Business course cover"><span>Business Training</span></div>
    <div class="tile t7" role="img" aria-label="Interview series cover"><span>Celebrity Interviews</span></div>
    <div class="tile t8" role="img" aria-label="Workout audio cover"><span>Fitness Programs</span></div>
  </div>

  <section class="band">
    <div class="point" style="left:27px"><h3>LISTEN YOUR ZARNO, TAVO<br>OR ORVEL DEVICE</h3><p>Lorem Ipsum is simply dummy text of the printing and typesetting industry. Lorem Ipsum has been the industry's</p></div>
    <div class="point" style="left:256px"><h3>ALL YOU CAN ENJOY FOR ONE<br>LOW MONTHLY PRICE</h3><p>Lorem Ipsum is simply dummy text of the printing and typesetting industry. Lorem Ipsum has been the industry's</p></div>
    <div class="point" style="left:485px"><h3>NO OBLIGATION<br>CANCEL ANY TIME</h3><p>Lorem Ipsum is simply dummy text of the printing and typesetting industry. Lorem Ipsum has been the industry's</p></div>
    <svg class="hex" style="left:11px" viewBox="0 0 34 36"><polygon points="17,0 34,9 34,27 17,36 0,27 0,9" fill="var(--navy)"/><rect x="9" y="11" width="16" height="13" rx="1.5" fill="none" stroke="#fff" stroke-width="2"/><rect x="22" y="14" width="5" height="9" fill="var(--navy)" stroke="#fff" stroke-width="1.5"/></svg>
    <svg class="hex" style="left:240px" viewBox="0 0 34 36"><polygon points="17,0 34,9 34,27 17,36 0,27 0,9" fill="var(--navy)"/><circle cx="17" cy="17" r="8" fill="none" stroke="#fff" stroke-width="2"/><text x="17" y="21" text-anchor="middle" font-family="Open Sans,sans-serif" font-weight="700" font-size="11" fill="#fff">$</text><rect x="13" y="26" width="8" height="3" fill="#fff"/></svg>
    <svg class="hex" style="left:469px" viewBox="0 0 34 36"><polygon points="17,0 34,9 34,27 17,36 0,27 0,9" fill="var(--navy)"/><path d="M10 10 L24 26 M24 10 L10 26" stroke="#fff" stroke-width="3" stroke-linecap="round"/></svg>
  </section>

  <h2 class="section-title" style="top:931px">Start Your Free Trail</h2>
  <p class="trial-copy">You will get instant &amp; unlimited access to all the material on Dunmoral for 14 days.<br>There is no obligation &amp; you can cancel at any time.</p>
  <p class="trial-note">Credit card Not Required For Free Trail</p>
  <div class="email">Enter your email address...</div>
  <a class="btn-access">Get Instant Access</a>
  <span class="or">— OR —</span>
  <a class="btn-social"><i></i>Sign Up Using Chatterly</a>

  <footer class="footer">
    <nav><a>About</a><b>|</b><a>Help</a><b>|</b><a>Contact Us</a><b>|</b><a>Member Login</a><b>|</b><a>Privacy Policy</a><b>|</b><a>Terms Of Services</a></nav>
    <span>Copyrights © 2014 Dunmoral LLC - All Rights Reserved</span>
  </footer>
</div>
</body>
</html>
```